Preliminary design concepts for VELURAN history document

To produce three design concepts as a demonstration for the layout of a document with a look and feel compatible with the existing documents/visual identity of an Australia-based NGO. The design concepts will be used to provide concepts to the NGO and ideally select a designer for the longer 30 - 50 page document.

Target Market(s)

Australian heritage community, international heritage community, general population interested in heritage issues and key stakeholders in heritage projects

Colors
0455a3
3176b5
85acd3
ffc214
fece3e
fee18a
f78f20
f37122

Requirements
Must have
• Eye catching but authoritative design to reflect a serious professional organisation, but one which reflects a modern, progressive approach.
• The designer needs to have experience working with document layout in InDesign and/or Illustrator and provide files in a range of outputs including EPS formats as well as HTML and PDF.
Nice to have
• Interplay between images and design elements

```html
<!DOCTYPE html>
<html lang="en">
<head>
<meta charset="utf-8">
<title>Innovation in Conservation — Cover</title>
<link href="https://fonts.googleapis.com/css2?family=Bebas+Neue&family=Oswald:wght@500&family=Roboto:wght@400;700&display=swap" rel="stylesheet">
<style>
  :root {
    --bg: #d9d9d9;
    --orange: #f37122;
    --orange-light: #f78f20;
    --navy: #2e3580;
    --white: #ffffff;
    --ink: #111111;
    --photo-dark: #3a3a3a;
    --photo-light: #e6e6e6;
  }
  * { margin: 0; padding: 0; box-sizing: border-box; }
  html, body { width: 1200px; height: 1200px; overflow: hidden; }
  body { background: var(--bg); display: flex; align-items: center; justify-content: center; }

  .cover {
    position: relative;
    width: 800px;
    height: 1130px;
    background: linear-gradient(160deg, var(--orange-light), var(--orange) 60%);
    overflow: hidden;
    box-shadow: 0 10px 30px rgba(0,0,0,0.2);
  }
  .cover-art { position: absolute; inset: 0; width: 100%; height: 100%; }

  .title-main {
    position: absolute;
    left: 0; right: 0; top: 548px;
    text-align: center;
    font-family: "Bebas Neue", sans-serif;
    font-weight: 400;
    font-size: 180px;
    line-height: 1;
    color: var(--navy);
    letter-spacing: 2px;
  }
  .title-sub {
    position: absolute;
    left: 0; right: 0; top: 716px;
    text-align: center;
    font-family: "Oswald", sans-serif;
    font-weight: 500;
    font-size: 56px;
    line-height: 1;
    letter-spacing: 15px;
    padding-left: 15px;
    color: var(--white);
  }
  .title-note {
    position: absolute;
    left: 0; right: 0; top: 796px;
    text-align: center;
    font-family: "Roboto", sans-serif;
    font-weight: 400;
    font-size: 22px;
    line-height: 1.2;
    color: var(--ink);
  }

  .brand {
    position: absolute;
    left: 0; right: 0; top: 905px;
    display: flex; align-items: center; justify-content: center; gap: 10px;
  }
  .brand-dot { width: 22px; height: 22px; border-radius: 50%; background: var(--navy); }
  .brand-name {
    font-family: "Roboto", sans-serif;
    font-weight: 700;
    font-size: 20px;
    letter-spacing: 1px;
    color: var(--navy);
  }
</style>
</head>
<body>
  <main class="cover">
    <svg class="cover-art" viewBox="0 0 800 1130">
      <defs>
        <clipPath id="photo-clip">
          <rect x="0" y="0" width="800" height="610"/>
        </clipPath>
        <linearGradient id="photo-tone" x1="0" y1="0" x2="0" y2="1">
          <stop offset="0" stop-color="#e6e6e6"/>
          <stop offset="0.45" stop-color="#9a9a9a"/>
          <stop offset="1" stop-color="#3a3a3a"/>
        </linearGradient>
      </defs>
      <circle class="cover-photo" role="img"
              aria-label="Black and white photograph of ruined stone engine houses on an open hillside"
              cx="400" cy="350" r="320" fill="url(#photo-tone)" clip-path="url(#photo-clip)"/>
      <g class="title-frame" fill="none" stroke="#ffffff" stroke-width="2">
        <path d="M68 640 H50 V870 H750 V640 H732"/>
      </g>
      <path class="base-band" d="M0 1035 Q 420 1000 800 905 L800 1130 L0 1130 Z" fill="#ffffff"/>
    </svg>

    <h1 class="title-main">INNOVATION</h1>
    <p class="title-sub">IN CONSERVATION</p>
    <p class="title-note">A brief history of Australia VELURAN<br>and the Kestrel Charter</p>

    <div class="brand">
      <span class="brand-dot"></span>
      <span class="brand-name">AUSTRALIA VELURAN</span>
    </div>
  </main>
</body>
</html>
```